RWT Fittings Ltd Business Cards

We need a business card with our business logo. We provide window and door installations on high-rises in west coast British Colombia, Canada.

I would like my business information and details on one side of the card, and the other side the company name with logo

Target Market(s)

General Contractors

Industry/Entity Type

Construction

Contact Information for Business Card

one side i want my company name and logo in the dark theme logo that i provided

Requirements
Must have
• Marco Peltieri, 16045518293, RWTFittings@mailbox-demo.com, 1407-5194 Linden Row Burnaby BC, V5H 2K9, Owner & Manager

```html
<!DOCTYPE html>
<html lang="en">
<head>
<meta charset="utf-8">
<title>RWT Fittings Ltd – Business Card</title>
<link href="https://fonts.googleapis.com/css2?family=Open+Sans:wght@400;600;700&display=swap" rel="stylesheet">
<style>
  :root {
    --stage-light: #5a5a5a;
    --stage-dark: #1a1a1a;
    --card-bg: #1b1b1b;
    --brand-blue: #29a8e0;
    --text-light: #e6e6e6;
    --text-muted: #bdbdbd;
    --pattern-top: #262626;
    --pattern-bottom: #141414;
  }
  * { box-sizing: border-box; margin: 0; padding: 0; }
  html, body { width: 1200px; height: 780px; overflow: hidden; }
  body {
    background: linear-gradient(135deg, var(--stage-light) 0%, #333 50%, var(--stage-dark) 100%);
    font-family: "Open Sans", Arial, sans-serif;
    position: relative;
  }
  .card {
    position: absolute;
    top: 235px;
    width: 540px;
    height: 310px;
    background: var(--card-bg);
    border-radius: 4px;
    box-shadow: 0 18px 40px rgba(0,0,0,.55);
    overflow: hidden;
  }
  .card--front { left: 40px; }
  .card--back { left: 620px; }

  .brand {
    position: absolute;
    display: flex;
    align-items: center;
    gap: 14px;
    color: var(--brand-blue);
    font-weight: 600;
    white-space: nowrap;
  }
  .card--front .brand { top: 40px; left: 0; right: 0; justify-content: center; font-size: 40px; }
  .brand__mark { width: 34px; height: 34px; background: var(--brand-blue); }

  .holder { position: absolute; top: 124px; left: 0; right: 0; text-align: center; }
  .holder__name {
    color: var(--brand-blue);
    font-weight: 700;
    font-size: 21px;
    letter-spacing: .5px;
    text-transform: uppercase;
  }
  .holder__role { color: var(--text-muted); font-size: 15px; margin-top: 2px; }

  .contact-rule { position: absolute; left: 30px; top: 200px; width: 480px; height: 40px; }
  .contact-list {
    position: absolute;
    top: 246px;
    left: 30px;
    width: 480px;
    display: grid;
    grid-template-columns: 110px 220px 150px;
    list-style: none;
    color: var(--text-light);
    font-size: 13px;
    line-height: 1.35;
  }
  .contact-list li { text-align: center; white-space: nowrap; }
  .contact-list__address { white-space: normal; }

  .back-pattern {
    position: absolute;
    inset: 0;
    background: linear-gradient(160deg, var(--pattern-top), var(--pattern-bottom));
  }
  .card--back .brand {
    top: 50%;
    left: 50%;
    transform: translate(-50%, -50%);
    font-size: 30px;
    gap: 10px;
  }
  .card--back .brand__mark { width: 24px; height: 24px; }
</style>
</head>
<body>

<section class="card card--front" aria-label="Business card front">
  <div class="brand">
    <span class="brand__mark"></span>
    <span class="brand__name">RWT Fittings Ltd</span>
  </div>

  <div class="holder">
    <p class="holder__name">Marco Peltieri</p>
    <p class="holder__role">Owner &amp; Manager</p>
  </div>

  <svg class="contact-rule" viewBox="0 0 480 40" aria-hidden="true">
    <line x1="0" y1="20" x2="480" y2="20" stroke="#29a8e0" stroke-width="1.5"/>
    <circle cx="55" cy="20" r="13" fill="#1b1b1b" stroke="#29a8e0" stroke-width="2"/>
    <path d="M50 13 q-3 2 -1 7 q3 6 8 7 q3 0 4 -2 l-3 -3 l-2 1 q-3 -1 -4 -5 l1 -2 z" fill="#29a8e0"/>
    <circle cx="220" cy="20" r="13" fill="#1b1b1b" stroke="#29a8e0" stroke-width="2"/>
    <rect x="212" y="15" width="16" height="11" fill="#29a8e0"/>
    <polyline points="212,15 220,22 228,15" fill="none" stroke="#1b1b1b" stroke-width="1.5"/>
    <circle cx="405" cy="20" r="13" fill="#1b1b1b" stroke="#29a8e0" stroke-width="2"/>
    <path d="M405 29 q-7 -8 -7 -13 a7 7 0 0 1 14 0 q0 5 -7 13 z" fill="#29a8e0"/>
    <circle cx="405" cy="16" r="2.6" fill="#1b1b1b"/>
  </svg>

  <ul class="contact-list">
    <li class="contact-list__phone">1 604 551 8293</li>
    <li class="contact-list__email">RWTFittings@mailbox-demo.com</li>
    <li class="contact-list__address">1407-5194 Linden Row<br>Burnaby BC, V5H 2K9</li>
  </ul>
</section>

<section class="card card--back" aria-label="Business card back">
  <div class="back-pattern" role="img" aria-label="Repeating dark tone-on-tone pattern of the company building symbol"></div>
  <div class="brand">
    <span class="brand__mark"></span>
    <span class="brand__name">RWT Fittings Ltd</span>
  </div>
</section>

</body>
</html>
```